VoRN Media Shredding professional postcard

I'm looking for a postcard design that tells a story in very few words about how important it is to protect yourself your family and your clients against sensitive information and identity theft. My website is vornmediashredding.net if you are looking for text to put on card. Would like "secure and certified destruction of your data and media" on the postcard.

Target Market(s)

Commercial and residential.

Industry/Entity Type

Business Service

Font styles to use
Serif

Colors
000000

Requirements
Must have
• A pic, 1-855-312-9048 phone number, vornmediashredding.net web address area for postage must be double sided. Definitely want it eye catching. Must have an area for postage and mailing address. Would like to see glossy on one side and the other side not glossy

```html
<!DOCTYPE html>
<html lang="en">
<head>
<meta charset="utf-8">
<title>VoRN Media Shredding Postcard</title>
<link rel="stylesheet" href="https://fonts.googleapis.com/css2?family=Open+Sans:wght@400;600;700&family=Quicksand:wght@700&display=swap">
<style>
  :root {
    --page: #d9d6d2;
    --card: #ffffff;
    --panel: #f1f1f1;
    --blue-dark: #0d4f9e;
    --blue: #0a63c2;
    --blue-light: #0a8ee0;
    --green: #8cc63f;
    --ink: #0a0a0a;
    --ink-soft: #2b2b2b;
    --grey: #c9c9cb;
    --teal: #0f7a6c;
    --line: #cfcfcf;
    --link: #36a9e8;
  }
  html, body {
    margin: 0;
    padding: 0;
    width: 955px;
    height: 1200px;
    overflow: hidden;
    background: var(--page);
  }
  .canvas {
    position: relative;
    width: 955px;
    height: 1200px;
  }
  .postcard {
    position: absolute;
    left: 47px;
    width: 860px;
    height: 540px;
    background: var(--card);
    box-shadow: 0 4px 12px rgba(0,0,0,.25);
  }
  .postcard--front { top: 40px; }
  .postcard--back { top: 620px; }
  .postcard svg { display: block; }
  .brand-name { font-family: 'Quicksand', sans-serif; font-weight: 700; }
  .copy { font-family: 'Open Sans', sans-serif; }
</style>
</head>
<body>
<main class="canvas">

  <!-- Front side -->
  <section class="postcard postcard--front">
    <svg width="860" height="540" viewBox="0 0 860 540">
      <defs>
        <linearGradient id="band-blue" x1="0" x2="1" y1="0" y2="0">
          <stop offset="0" stop-color="var(--blue-dark)"/>
          <stop offset="1" stop-color="var(--blue-light)"/>
        </linearGradient>
        <radialGradient id="hero-tones" cx="0.45" cy="0.5" r="0.7">
          <stop offset="0" stop-color="#9fd3f2"/>
          <stop offset="0.35" stop-color="#3f6f96"/>
          <stop offset="1" stop-color="#141a22"/>
        </radialGradient>
        <linearGradient id="truck-tones" x1="0" x2="1">
          <stop offset="0" stop-color="#7a5a48"/>
          <stop offset="0.5" stop-color="#e8e6e3"/>
          <stop offset="1" stop-color="#a25a52"/>
        </linearGradient>
        <linearGradient id="drive-tones" x1="0" x2="1" y1="0" y2="1">
          <stop offset="0" stop-color="#f2f2f2"/>
          <stop offset="1" stop-color="#8d939a"/>
        </linearGradient>
        <clipPath id="hero-clip"><circle cx="830" cy="300" r="420"/></clipPath>
        <clipPath id="green-arc-clip"><rect x="0" y="110" width="860" height="385"/></clipPath>
        <clipPath id="black-arc-clip"><rect x="0" y="0" width="860" height="80"/></clipPath>
      </defs>

      <rect class="light-panel" x="0" y="0" width="860" height="495" fill="var(--panel)"/>

      <!-- Brand -->
      <circle cx="185" cy="72" r="42" fill="none" stroke="var(--green)" stroke-width="4"/>
      <text class="brand-name" x="185" y="165" font-size="31" fill="var(--blue-dark)" text-anchor="middle">VoRN Media Shredding</text>

      <!-- Headline band -->
      <rect x="0" y="190" width="420" height="165" fill="url(#band-blue)"/>
      <text class="copy" x="188" y="248" font-size="27" font-weight="600" fill="#fff" text-anchor="middle">SECURE AND CERTIFIED</text>
      <text class="copy" x="188" y="284" font-size="27" font-weight="600" fill="#fff" text-anchor="middle">DESTRUCTION OF YOUR</text>
      <text class="copy" x="188" y="320" font-size="27" font-weight="600" fill="#fff" text-anchor="middle">DATA AND MEDIA</text>

      <!-- Service circles -->
      <circle cx="76" cy="425" r="54" fill="#fff" stroke="var(--blue-dark)" stroke-width="3"/>
      <circle cx="76" cy="425" r="48" fill="var(--teal)"/>
      <circle cx="213" cy="425" r="54" fill="#fff" stroke="var(--blue-dark)" stroke-width="3"/>
      <circle cx="213" cy="425" r="48" fill="url(#truck-tones)" role="img" aria-label="Mobile shredding truck parked on site"/>
      <circle cx="340" cy="425" r="54" fill="#fff" stroke="var(--blue-dark)" stroke-width="3"/>
      <circle cx="340" cy="425" r="48" fill="url(#drive-tones)" role="img" aria-label="Stack of hard drives ready for destruction"/>

      <!-- Curved accents -->
      <circle cx="830" cy="300" r="450" fill="none" stroke="var(--green)" stroke-width="13" clip-path="url(#green-arc-clip)"/>
      <circle cx="830" cy="300" r="436" fill="none" stroke="var(--ink)" stroke-width="12" clip-path="url(#black-arc-clip)"/>

      <!-- Hero image -->
      <rect x="400" y="0" width="460" height="495" fill="url(#hero-tones)" clip-path="url(#hero-clip)" role="img" aria-label="Businessman holding a glowing globe linked to laptop, tablet and phone"/>

      <!-- Bottom bar -->
      <rect x="0" y="495" width="860" height="45" fill="var(--ink)"/>
      <text class="copy" x="430" y="531" font-size="36" font-weight="600" fill="#fff" text-anchor="middle" letter-spacing="2.5">ALL SERVICES DONE AT YOUR LOCATION</text>
    </svg>
  </section>

  <!-- Back side -->
  <section class="postcard postcard--back">
    <svg width="860" height="540" viewBox="0 0 860 540">
      <defs>
        <linearGradient id="info-blue" x1="0" x2="1">
          <stop offset="0" stop-color="var(--blue-dark)"/>
          <stop offset="1" stop-color="var(--blue-light)"/>
        </linearGradient>
        <linearGradient id="info-black" x1="0" x2="1">
          <stop offset="0" stop-color="var(--ink)"/>
          <stop offset="1" stop-color="#3a3a3a"/>
        </linearGradient>
        <clipPath id="info-clip"><circle cx="20" cy="290" r="410"/></clipPath>
        <clipPath id="back-green-clip"><rect x="0" y="130" width="860" height="410"/></clipPath>
        <clipPath id="back-black-clip"><rect x="0" y="0" width="860" height="105"/></clipPath>
      </defs>

      <!-- Accent arcs -->
      <circle cx="20" cy="290" r="422" fill="none" stroke="var(--green)" stroke-width="14" clip-path="url(#back-green-clip)"/>
      <circle cx="20" cy="290" r="418" fill="none" stroke="var(--ink)" stroke-width="12" clip-path="url(#back-black-clip)"/>

      <g class="info-panel" clip-path="url(#info-clip)">
        <rect x="0" y="0" width="440" height="150" fill="var(--panel)"/>
        <rect x="0" y="150" width="440" height="200" fill="url(#info-blue)"/>
        <rect x="0" y="350" width="440" height="100" fill="var(--grey)"/>
        <rect x="0" y="450" width="440" height="90" fill="url(#info-black)"/>
      </g>

      <!-- Brand -->
      <circle cx="182" cy="58" r="38" fill="none" stroke="var(--green)" stroke-width="4"/>
      <text class="brand-name" x="182" y="131" font-size="24" fill="var(--blue-dark)" text-anchor="middle">VoRN Media Shredding</text>

      <!-- Message -->
      <text class="copy" x="182" y="179" font-size="16" font-weight="600" fill="#fff" text-anchor="middle">SECURE AND CERTIFIED DESTRUCTION</text>
      <text class="copy" x="182" y="200" font-size="16" font-weight="600" fill="#fff" text-anchor="middle">OF YOUR DATA AND MEDIA</text>
      <g class="copy" font-size="12" fill="#fff" text-anchor="middle">
        <text x="182" y="232">Whether you are a small business, large business, or</text>
        <text x="182" y="246">individual, the confidential information stored on devices</text>
        <text x="182" y="260">that you use can cause potential and significant issues if it</text>
        <text x="182" y="274">falls into the wrong hands.</text>
        <text x="182" y="304">Serving Long Island and Tri State Area</text>
      </g>

      <!-- Phone pill -->
      <rect x="27" y="320" width="314" height="43" rx="5" fill="var(--ink-soft)"/>
      <circle cx="91" cy="342" r="12" fill="none" stroke="#fff" stroke-width="2"/>
      <path d="M86 335 q-3 2 0 7 q3 6 8 7 q3 1 4 -2 l-3 -3 l-2 1 q-3 -2 -4 -5 l1 -2 z" fill="#fff"/>
      <text class="copy" x="114" y="350" font-size="21" fill="#fff">1-855-312-9048</text>

      <g class="copy" font-size="11.5" fill="var(--ink)" text-anchor="middle">
        <text x="182" y="392">You need to properly secure, safeguard and</text>
        <text x="182" y="406">destroy hard drives, flash drives, and other electronic media</text>
        <text x="182" y="420">that store critical, sensitive or personal information</text>
      </g>

      <text class="copy" x="40" y="484" font-size="11" fill="#fff">FOR MORE INFORMATION PLEASE CONTACT US</text>
      <path d="M25 502 l16 6 l-7 2 l-2 7 z" fill="var(--link)"/>
      <text class="copy" x="50" y="516" font-size="17" fill="var(--link)">www.vornmediashredding.net</text>

      <!-- Postage and address -->
      <rect class="stamp-box" x="705" y="24" width="123" height="84" fill="none" stroke="var(--line)" stroke-width="1.5"/>
      <g class="address-lines" stroke="var(--line)" stroke-width="1.5">
        <line x1="514" y1="220" x2="828" y2="220"/>
        <line x1="514" y1="277" x2="828" y2="277"/>
        <line x1="514" y1="335" x2="828" y2="335"/>
        <line x1="514" y1="392" x2="828" y2="392"/>
      </g>
    </svg>
  </section>

</main>
</body>
</html>
```